Supplement Brand Product Labels

Product Label for Supplement Brand

Protein Powder Label (2 x different flavours)

Neon Colours / Skull / Spooky
Refer to pictures below, they are the look we are wanting to go with but put our touch to it aswell.

Target Market(s)

Fitness

Industry/Entity Type

Supplement Brand

Colors
0054AA
0677BA
7BADD7
CADEEF
E8F1F8
0094D4
00A9DD
6FCCEA
C7EBF8
E9F6FB
00AB8E
00BBA5
67D7C9
C6EFE9
E9F9F6
59FF00
82FF00
B8FF75
E3FFCB
F4FFEA
FFF300
FFF600
FEFA6F
FFFEC7
FFFEE8
FFC000
F8CF3A
FAE287
FDF2CF
FEFAEE
F0912C
F2A743
F7CA91
FBE8D2
FDF5EE
EE7325
F08F49
F5BC92
FAE3D3
FDF4ED
EB3D1F
EC4F4E
F09395
F8D3D4
FCEDEE
E54698
E96AAD
F1A4CE
F9D9EA
FCEFF6
A7469A
B969AE
D3A5CF
EDDBEB
F8F0F9
6B429C
8869AF
B7A5CE
E3DAEB
F3F0F8

Requirements
Nice to have
• Skull, Neon Colours, Abstract, Barbell, Lighting Bolt, Flames, Spooky

```html
<!DOCTYPE html>
<html lang="en">
<head>
<meta charset="utf-8">
<title>Protein Powder Label – Back Panel</title>
<link rel="stylesheet" href="https://fonts.googleapis.com/css2?family=Open+Sans:wght@400;600;700;800&display=swap">
<style>
  :root{
    --ink:#ffffff;
    --ink-soft:#f3e6f2;
    --bg-deep:#4a2766;
    --bg-violet:#7b3b8f;
    --bg-magenta:#c4428f;
    --bg-pink:#e05aa3;
    --bg-olive:#a99a3b;
    --rule:#ffffff;
  }
  *{box-sizing:border-box;margin:0;padding:0}
  html,body{width:1016px;height:1200px;overflow:hidden}
  body{font-family:"Open Sans",sans-serif;color:var(--ink);background:var(--bg-deep)}
  .label{position:relative;width:1016px;height:1200px;overflow:hidden}
  .artwork{position:absolute;inset:0;
    background:
      radial-gradient(ellipse 340px 420px at 520px 430px, var(--bg-pink) 0%, rgba(196,66,143,.6) 45%, transparent 80%),
      radial-gradient(ellipse 420px 300px at 1000px 20px, var(--bg-olive) 0%, rgba(169,154,59,.4) 40%, transparent 75%),
      linear-gradient(180deg, var(--bg-violet) 0%, #8a3d8f 40%, #9a3f90 65%, var(--bg-deep) 100%);}
  .block{position:absolute}
  /* nutrition panel */
  .nutrition{left:81px;top:86px;width:560px;font-size:16px}
  .nutrition .row{display:grid;grid-template-columns:230px 160px 170px;align-items:start}
  .nutrition .head{font-weight:700;font-size:15px;line-height:19px;margin-bottom:22px}
  .nutrition .head span:nth-child(n+2){text-align:center}
  .nutrition .data{height:48.7px}
  .nutrition .data span:nth-child(2){text-align:right;padding-right:38px}
  .nutrition .data span:nth-child(3){text-align:right;padding-right:42px}
  .nutrition .sub span:first-child{padding-left:17px}
  /* copy */
  .section-title{font-weight:700;font-size:21px;margin-bottom:10px}
  .section-body{font-size:14.5px;line-height:23px}
  .ingredients{left:81px;top:528px;width:560px}
  .allergens{left:81px;top:670px;width:560px}
  .directions{left:81px;top:754px;width:560px}
  .disclaimer{left:81px;top:868px;width:860px;font-size:14.5px;line-height:25px}
  .storage{left:81px;top:960px;font-weight:700;font-size:15px}
  /* amino panel */
  .amino{left:698px;top:80px;width:252px}
  .amino h2{font-weight:800;font-size:18.5px;letter-spacing:.2px;margin-bottom:12px}
  .amino .th{display:flex;justify-content:space-between;font-weight:700;font-size:14.5px;padding:0 2px 6px 2px;border-bottom:2px solid var(--rule);margin-bottom:10px}
  .amino .tr{display:flex;justify-content:space-between;font-size:14.5px;height:35.8px;padding:0 2px}
  /* footer */
  .code-box{left:700px;top:970px;width:233px;height:168px;border:2.5px solid var(--ink)}
  .brand{left:94px;top:1048px;display:flex;align-items:center;gap:12px;font-weight:800;font-size:30px;line-height:1}
  .brand-mark{width:22px;height:22px;border-radius:50%;background:var(--ink)}
  .origin-badge{left:453px;top:1094px;width:200px;height:44px;border-radius:6px;background:var(--ink)}
</style>
</head>
<body>
<main class="label">
  <div class="artwork" role="img" aria-label="Neon purple and magenta illustrated skull artwork filling the label background"></div>

  <section class="block nutrition">
    <div class="row head"><span>6.25 Servings Per 500g Packet<br>80 Grams Per Serve</span><span>Average Quantity<br>Per Serving</span><span>Average Quantity<br>Per 100g</span></div>
    <div class="row data"><span>Energy (KJ)</span><span>1286</span><span>1608</span></div>
    <div class="row data"><span>Protein (G)</span><span>24.3</span><span>30.4</span></div>
    <div class="row data"><span>Fat, Total (G)</span><span>1.7</span><span>2.1</span></div>
    <div class="row data sub"><span>Saturated (G)</span><span>1.1</span><span>1.3</span></div>
    <div class="row data"><span>Carbohydrates (G)</span><span>47.6</span><span>59.5</span></div>
    <div class="row data sub"><span>Sugar (G)</span><span>3.5</span><span>4.4</span></div>
    <div class="row data"><span>Sodium (MG)</span><span>68</span><span>85</span></div>
  </section>

  <section class="block ingredients">
    <h3 class="section-title">Ingredients</h3>
    <p class="section-body">Maltodextrin, Whey Protein Concentrate, Milk Protein Isolate, Whey Protein Isolate, Branch Chain Amino Acids, Albumin, Wheaten Cornflour, Wholemeal Flour, Cocoa, Flavour, Sucralose.</p>
  </section>

  <section class="block allergens">
    <h3 class="section-title">Allergens</h3>
    <p class="section-body">Egg, Milk, Soy, Wheat, Gluten.</p>
  </section>

  <section class="block directions">
    <h3 class="section-title">Directions Of Use</h3>
    <p class="section-body">Mix 2 heaped scoop (40 grams) with 250ml of water or milk and consume immediately. For optimal results, consume 2 – 3 times per day.</p>
  </section>

  <p class="block disclaimer">Formulated supplementary sports food. Not suitable for children under 15 years of age or pregnant women. Should only be used under medical or dietetic supervision. This product is not a sole source of nutrition and should be consumed in conjunction with a nutritious diet and appropriate physical training or exercise program.</p>

  <p class="block storage">Store in a cool dry place out of direct sunlight.</p>

  <section class="block amino">
    <h2>Typical Amino Acid Profile</h2>
    <div class="th"><span>Amino Acid</span><span>MG/100G</span></div>
    <div class="tr"><span>Alanine (mg)</span><span>1619</span></div>
    <div class="tr"><span>Arginine (mg)</span><span>920</span></div>
    <div class="tr"><span>Aspartic Acid (mg)</span><span>3564</span></div>
    <div class="tr"><span>Cystine (mg)</span><span>771</span></div>
    <div class="tr"><span>Glutamic Acid (mg)</span><span>5863</span></div>
    <div class="tr"><span>Glycine (mg)</span><span>620</span></div>
    <div class="tr"><span>Histidine (mg)</span><span>628</span></div>
    <div class="tr"><span>Isoleucine (mg)</span><span>1861</span></div>
    <div class="tr"><span>Leucine (mg)</span><span>3480</span></div>
    <div class="tr"><span>Lysine (mg)</span><span>2913</span></div>
    <div class="tr"><span>Methionine (mg)</span><span>792</span></div>
    <div class="tr"><span>Phenylalanine (mg)</span><span>1154</span></div>
    <div class="tr"><span>Proline (mg)</span><span>2400</span></div>
    <div class="tr"><span>Serine (mg)</span><span>1803</span></div>
    <div class="tr"><span>Threonine (mg)</span><span>2238</span></div>
    <div class="tr"><span>Tryptophan (mg)</span><span>529</span></div>
    <div class="tr"><span>Tyrosine (mg)</span><span>1112</span></div>
    <div class="tr"><span>Valine (mg)</span><span>1759</span></div>
  </section>

  <div class="block code-box" aria-hidden="true"></div>

  <div class="block brand"><span class="brand-mark"></span><span>Voltgrave Nutrition</span></div>

  <div class="block origin-badge" role="img" aria-label="Country of origin badge"></div>
</main>
</body>
</html>
```